full stationary design for a modern sleek design company

we are a design company that does modern minimalistic interior design works as well as other design services for high end clients.
we need a full stationary design including and not limited to (double sided business card, letter head, envelopes, documents folder...etc) that reflects the modern style design we do.
sleek modern and minimalistic is the requirements.
Updates

please use the latest attached files as there was a slight modification on the logo Added Wednesday, March 1, 2017

minor update on the logo files in JPG and PSD has been updated kindly follow the new attachments. Added Thursday, March 2, 2017

Target Market(s)

modern minimalist clients

Industry/Entity Type

Design Agency

Requirements
Must have
• the logo
Nice to have
• i like the colors in the colored 3D logo attached
Should not have
• too many colors

```html
<!DOCTYPE html>
<html lang="en">
<head>
<meta charset="utf-8">
<title>Norde Studio — Stationery Set</title>
<link href="https://fonts.googleapis.com/css2?family=Montserrat:wght@600&family=Open+Sans:wght@400;700&display=swap" rel="stylesheet">
<style>
  :root{
    --bg:#f0f0f0;
    --paper:#ffffff;
    --charcoal:#3a3a3a;
    --orange:#e8962a;
    --ink:#555555;
    --light:#f2f2f2;
  }
  *{margin:0;padding:0;box-sizing:border-box}
  html,body{width:1200px;height:903px;overflow:hidden;background:var(--bg)}
  body{position:relative;font-family:"Open Sans",Arial,sans-serif;color:var(--ink)}
  .piece{position:absolute}
  .paper{background:var(--paper)}
  .dark{background:var(--charcoal)}

  .brand{display:flex;align-items:center;gap:5px;font-family:"Montserrat",Arial,sans-serif;font-weight:600;text-transform:uppercase;letter-spacing:.06em;white-space:nowrap;color:var(--charcoal)}
  .brand-mark{background:var(--orange);flex:none}
  .brand.on-dark{color:var(--light)}

  .contact{list-style:none;font-size:5.2px;line-height:7.4px;color:var(--ink)}
  .contact li{display:flex;align-items:center;gap:3px}
  .contact svg{flex:none}

  /* letterhead */
  .letterhead{left:187px;top:63px;width:372px;height:524px}
  .letterhead .brand{position:absolute;left:33px;top:40px;font-size:10px}
  .letterhead .brand-mark{width:11px;height:11px}
  .letterhead .contact{position:absolute;left:273px;top:26px}

  /* folder */
  .folder{left:623px;top:38px;width:435px;height:554px}
  .folder .spine{position:absolute;left:0;top:0;width:12px;height:100%;background:#333}
  .folder .brand{position:absolute;left:76px;top:256px;font-size:26px}
  .folder .brand-mark{width:30px;height:30px}

  /* business cards */
  .card-front{left:60px;top:649px;width:165px;height:93px;border-radius:0 46px 46px 0;padding:17px 15px}
  .card-name{font-size:7px;font-weight:700;color:var(--orange);line-height:8px}
  .card-role{font-size:5px;color:#ddd;margin-bottom:6px}
  .card-front .contact{color:#ddd;font-size:4.6px;line-height:6.3px}
  .card-back{left:60px;top:754px;width:165px;height:94px;border-radius:46px 0 0 46px;display:flex;align-items:center;justify-content:center}
  .card-back .brand{font-size:8.5px;margin-left:14px}
  .card-back .brand-mark{width:9px;height:9px}

  /* envelopes */
  .envelope-front{left:265px;top:648px;width:415px;height:198px}
  .envelope-front .brand{position:absolute;left:25px;top:22px;font-size:9.5px}
  .envelope-front .brand-mark{width:10px;height:10px}
  .envelope-front .address{position:absolute;left:25px;top:38px;font-size:5px}
  .envelope-back{left:721px;top:648px;width:415px;height:198px}
  .envelope-back .flap{position:absolute;left:0;top:0;width:100%;height:70px}
  .envelope-back .brand{position:absolute;left:141px;top:25px;font-size:10px}
  .envelope-back .brand-mark{width:11px;height:11px}
</style>
</head>
<body>

<section class="piece paper letterhead" aria-label="Letterhead">
  <div class="brand"><span class="brand-mark"></span>Norde Studio</div>
  <ul class="contact">
    <li>14 Harbor Row</li>
    <li>Portland, Maine 04101</li>
    <li><svg width="5" height="5" viewBox="0 0 10 10"><path d="M2 1l2 2-1 1.5c.8 1.5 1.5 2.2 3 3L7.5 6l2 2-1.5 1.5C4 9 1 6 .5 2.5z" fill="var(--orange)"/></svg>(207) 555 0142</li>
    <li><svg width="5" height="5" viewBox="0 0 10 10"><rect x="2.5" y="0.5" width="5" height="9" rx="1" fill="none" stroke="var(--orange)"/></svg>(207) 555 0187</li>
    <li><svg width="5" height="5" viewBox="0 0 10 10"><rect x="0.5" y="2" width="9" height="6" fill="var(--orange)"/></svg>hello@nordestudio.com</li>
    <li><svg width="5" height="5" viewBox="0 0 10 10"><circle cx="5" cy="5" r="4.5" fill="var(--orange)"/></svg>www.nordestudio.com</li>
  </ul>
</section>

<section class="piece dark folder" aria-label="Document folder">
  <div class="spine"></div>
  <div class="brand on-dark"><span class="brand-mark"></span>Norde Studio</div>
</section>

<section class="piece dark card-front" aria-label="Business card front">
  <p class="card-name">ADAM KERR</p>
  <p class="card-role">CEO&amp;Founder</p>
  <ul class="contact">
    <li>14 Harbor Row</li>
    <li>Portland, Maine 04101</li>
    <li><svg width="4" height="4" viewBox="0 0 10 10"><path d="M2 1l2 2-1 1.5c.8 1.5 1.5 2.2 3 3L7.5 6l2 2-1.5 1.5C4 9 1 6 .5 2.5z" fill="var(--orange)"/></svg>(207) 555 0142</li>
    <li><svg width="4" height="4" viewBox="0 0 10 10"><rect x="2.5" y="0.5" width="5" height="9" rx="1" fill="none" stroke="var(--orange)"/></svg>(207) 555 0187</li>
    <li><svg width="4" height="4" viewBox="0 0 10 10"><rect x="0.5" y="2" width="9" height="6" fill="var(--orange)"/></svg>adam@nordestudio.com</li>
    <li><svg width="4" height="4" viewBox="0 0 10 10"><circle cx="5" cy="5" r="4.5" fill="var(--orange)"/></svg>www.nordestudio.com</li>
  </ul>
</section>

<section class="piece paper card-back" aria-label="Business card back">
  <div class="brand"><span class="brand-mark"></span>Norde Studio</div>
</section>

<section class="piece paper envelope-front" aria-label="Envelope front">
  <div class="brand"><span class="brand-mark"></span>Norde Studio</div>
  <p class="address">14 Harbor Row, Portland, Maine 04101</p>
</section>

<section class="piece paper envelope-back" aria-label="Envelope back">
  <div class="flap dark"></div>
  <div class="brand on-dark"><span class="brand-mark"></span>Norde Studio</div>
</section>

</body>
</html>
```